New Webpage for High Class Expert Witness Services Company

We are looking for a minimalist design for a webpage that just has our logo and an entry form offer to connect with one of our Liaisons.
The entry form should just ask for Name, Email, Contact Info and Description of Project.

Company Name is: The Marlowe Crest Advisory Services

Number of Pages Required

1 page

```html
<!DOCTYPE html>
<html lang="en">
<head>
<meta charset="utf-8">
<title>The Marlowe Crest Advisory Services</title>
<link href="https://fonts.googleapis.com/css2?family=Cinzel:wght@400;600;700&family=Lato:wght@400;700&display=swap" rel="stylesheet">
<style>
  :root {
    --ink: #0a0a0a;
    --paper: #ffffff;
    --hero-deep: #0b1a24;
    --hero-mid: #173644;
    --hero-teal: #1f4f5c;
    --frost: rgba(255,255,255,0.72);
    --field-line: rgba(255,255,255,0.8);
    --silver-hi: #e4e4e6;
    --silver-lo: #8e8f94;
    --photo-blue: #1b3f78;
    --photo-pink: #c2387f;
  }
  * { margin: 0; padding: 0; box-sizing: border-box; }
  html, body { width: 928px; height: 1200px; overflow: hidden; background: var(--paper); }
  body { position: relative; font-family: "Lato", sans-serif; color: var(--ink); }

  .hero {
    position: absolute; left: 0; top: 0; width: 928px; height: 570px;
    background: linear-gradient(100deg, #1d2c38 0%, var(--hero-deep) 35%, var(--hero-mid) 70%, var(--hero-teal) 100%);
  }
  .hero-photo { position: absolute; inset: 0; }
  .hero-cut { position: absolute; left: 0; top: 0; }

  .brand {
    position: absolute; left: 0; width: 928px; text-align: center;
    font-family: "Cinzel", serif; font-weight: 600; color: var(--silver-hi);
    white-space: nowrap;
  }
  .brand-mark { display: inline-block; background: var(--silver-hi); vertical-align: middle; }
  .brand-top { top: 43px; font-size: 22px; letter-spacing: 1px; line-height: 28px; }
  .brand-top .brand-mark { width: 14px; height: 14px; margin-right: 10px; margin-top: -4px; }

  .consult {
    position: absolute; left: 182px; top: 180px; width: 565px; height: 241px;
    border: 1px solid var(--frost); border-radius: 12px;
    background: rgba(10,20,28,0.25);
  }
  .consult-title { position: absolute; top: 15px; width: 100%; text-align: center; font-family: "Cinzel", serif; font-weight: 600; font-size: 23px; color: var(--paper); }
  .consult-sub { position: absolute; top: 44px; width: 100%; text-align: center; font-size: 12px; color: var(--paper); }
  .field {
    position: absolute; height: 30px; border: 1px solid var(--field-line); border-radius: 3px;
    font-size: 10px; letter-spacing: 2px; color: var(--paper); padding-left: 16px; line-height: 28px;
  }
  .field-name { left: 41px; top: 85px; width: 236px; }
  .field-email { left: 286px; top: 85px; width: 236px; }
  .field-contact { left: 41px; top: 126px; width: 482px; }
  .field-desc { left: 41px; top: 167px; width: 482px; }
  .submit {
    position: absolute; left: 401px; top: 403px; width: 126px; height: 32px; border-radius: 16px;
    background: linear-gradient(180deg, var(--silver-hi), var(--silver-lo));
    font-family: "Cinzel", serif; font-weight: 600; font-size: 13px; letter-spacing: 1px; color: #111;
    text-align: center; line-height: 32px;
  }
  .connector { position: absolute; left: 464px; top: 452px; width: 1px; height: 118px; background: #555; }

  .headline { position: absolute; top: 604px; width: 928px; text-align: center; font-family: "Cinzel", serif; font-weight: 700; font-size: 46px; line-height: 51px; letter-spacing: 1px; }
  .divider { position: absolute; left: 325px; top: 724px; }
  .motto { position: absolute; top: 751px; width: 928px; text-align: center; font-family: "Cinzel", serif; font-size: 19px; letter-spacing: 1px; }

  .about { position: absolute; left: 95px; top: 833px; width: 320px; text-align: center; font-size: 11px; line-height: 16.5px; color: #1c1c1c; }
  .about p + p { margin-top: 16px; }
  .about-photo {
    position: absolute; left: 447px; top: 793px; width: 370px; height: 210px; border-radius: 8px;
    background: linear-gradient(120deg, var(--photo-blue) 0%, #2a5aa0 45%, var(--photo-pink) 80%, #3a2a5a 100%);
  }

  .footer { position: absolute; left: 0; top: 1035px; width: 928px; height: 165px; background: var(--ink); }
  .brand-foot { top: 40px; font-size: 18px; letter-spacing: 1px; line-height: 24px; }
  .brand-foot .brand-mark { width: 11px; height: 11px; margin-right: 8px; margin-top: -3px; }
  .social { position: absolute; top: 101px; left: 409px; display: flex; gap: 15px; }
  .social span { width: 16px; height: 16px; border-radius: 50%; background: var(--paper); }
  .copyright { position: absolute; top: 134px; width: 928px; text-align: center; font-size: 10px; color: var(--paper); }
</style>
</head>
<body>
  <section class="hero">
    <div class="hero-photo" role="img" aria-label="Dim photo of a scientist in a lab coat and safety glasses working at a glowing data wall"></div>
    <svg class="hero-cut" width="928" height="570" viewBox="0 0 928 570" aria-hidden="true">
      <polygon points="0,548 928,498 928,570 0,570" fill="#050505"/>
      <polygon points="0,569 928,498 928,570 0,570" fill="#ffffff"/>
    </svg>

    <header class="brand brand-top"><i class="brand-mark"></i>Marlowe Crest Advisory Services</header>

    <form class="consult">
      <h2 class="consult-title">Request a Consultation</h2>
      <p class="consult-sub">Connect with one of our liaisons to discuss your matter in confidence.</p>
      <div class="field field-name">NAME</div>
      <div class="field field-email">EMAIL</div>
      <div class="field field-contact">CONTACT INFO</div>
      <div class="field field-desc">DESCRIPTION OF PROJECT</div>
    </form>
    <div class="submit">SUBMIT</div>
  </section>
  <div class="connector"></div>

  <h1 class="headline">THE MARLOWE CREST<br>ADVISORY SERVICES</h1>
  <svg class="divider" width="277" height="10" viewBox="0 0 277 10" aria-hidden="true">
    <line x1="0" y1="5" x2="127" y2="5" stroke="#333" stroke-width="1"/>
    <circle cx="139" cy="5" r="3.5" fill="#000"/>
    <line x1="150" y1="5" x2="277" y2="5" stroke="#333" stroke-width="1"/>
  </svg>
  <p class="motto">PRECISION. DISCRETION. EXPERTISE.</p>

  <div class="about">
    <p>At The Marlowe Crest Advisory Services, we provide elite expert witness and defense consulting for complex, high-stakes cases. Our network of seasoned professionals delivers clear, defensible insights where they matter most.</p>
    <p>We work with law firms, corporations, and private clients who require uncompromising standards, absolute confidentiality, and authoritative expertise.</p>
  </div>
  <div class="about-photo" role="img" aria-label="Photo of an analyst wearing a headset at monitors full of neon blue and pink data dashboards"></div>

  <footer class="footer">
    <div class="brand brand-foot"><i class="brand-mark"></i>Marlowe Crest Advisory Services</div>
    <div class="social" aria-label="Social links"><span></span><span></span><span></span><span></span></div>
    <p class="copyright">© 2026 | www.marlowecrestadvisory.com</p>
  </footer>
</body>
</html>
```